North Carolina-themed postcard

Would like 3x distinct designs for a postcard (sized 4.5 x 5.5) that celebrates the state of North Carolina. A vintage theme, a modern theme, and a simple black/white theme would be suggestions for design styles.

```html
<!DOCTYPE html>
<html lang="en">
<head>
<meta charset="utf-8">
<title>North Carolina Postcard</title>
<link rel="stylesheet" href="https://fonts.googleapis.com/css2?family=Great+Vibes&family=Chewy&display=swap">
<style>
  :root {
    --backdrop: #d6d6d6;
    --card-white: #f7f7f7;
    --ink-line: #333333;
    --band-navy: #1f3f7a;
    --band-blue: #3a68a8;
    --accent-green: #7cc242;
    --script-navy: #27346b;
    --script-red: #c8344a;
    --letter-shadow: #ec7f86;
    --letter-outline: #ffffff;
  }
  * { margin: 0; padding: 0; box-sizing: border-box; }
  html, body {
    width: 1200px; height: 696px; overflow: hidden;
    background: var(--backdrop);
  }
  .canvas { position: relative; width: 1200px; height: 696px; }
  .postcard {
    position: absolute; top: 155px;
    width: 540px; height: 386px;
    background: var(--card-white);
    box-shadow: 0 6px 18px rgba(0,0,0,0.25);
    overflow: hidden;
  }
  .postcard--back { left: 40px; }
  .postcard--front { left: 620px; }
  .postcard svg { display: block; width: 540px; height: 386px; }
  .greeting-script {
    font-family: "Great Vibes", cursive;
    fill: url(#scriptTone);
  }
  .state-name {
    font-family: "Chewy", sans-serif;
    font-size: 62px;
    letter-spacing: 1px;
  }
  .state-name--shadow { fill: var(--letter-shadow); }
  .state-name--fill {
    fill: url(#cityFill);
    stroke: var(--letter-outline);
    stroke-width: 2;
    paint-order: stroke;
  }
</style>
</head>
<body>
<main class="canvas">

  <section class="postcard postcard--back" aria-label="Postcard back">
    <svg viewBox="0 0 540 386" xmlns="http://www.w3.org/2000/svg">
      <defs>
        <linearGradient id="capitolFade" x1="0" y1="0" x2="1" y2="1">
          <stop offset="0" stop-color="#ececec"/>
          <stop offset="0.5" stop-color="#dcdcdc"/>
          <stop offset="1" stop-color="#e6e6e6"/>
        </linearGradient>
      </defs>
      <rect class="back-photo" width="540" height="386" fill="url(#capitolFade)"
            role="img" aria-label="Faded grayscale photo of the state capitol building with a statue in front"/>
      <line class="divider" x1="275" y1="40" x2="275" y2="340" stroke="var(--ink-line)" stroke-width="1.2"/>
      <rect class="stamp-box" x="420" y="34" width="100" height="70" fill="none" stroke="var(--ink-line)" stroke-width="1.5"/>
      <g class="address-lines" stroke="var(--ink-line)" stroke-width="1.2">
        <line x1="295" y1="170" x2="515" y2="170"/>
        <line x1="295" y1="205" x2="515" y2="205"/>
        <line x1="295" y1="240" x2="515" y2="240"/>
        <line x1="295" y1="275" x2="515" y2="275"/>
      </g>
    </svg>
  </section>

  <section class="postcard postcard--front" aria-label="Postcard front">
    <svg viewBox="0 0 540 386" xmlns="http://www.w3.org/2000/svg">
      <defs>
        <linearGradient id="aerialTone" x1="0" y1="0" x2="1" y2="1">
          <stop offset="0" stop-color="#e4edf3"/>
          <stop offset="0.45" stop-color="#c9d9c8"/>
          <stop offset="1" stop-color="#d7e3ee"/>
        </linearGradient>
        <linearGradient id="bandTone" x1="0" y1="0" x2="0" y2="1">
          <stop offset="0" stop-color="var(--band-navy)"/>
          <stop offset="1" stop-color="var(--band-blue)"/>
        </linearGradient>
        <linearGradient id="badgeTone" x1="0" y1="0" x2="1" y2="1">
          <stop offset="0" stop-color="#ffffff"/>
          <stop offset="0.55" stop-color="#f1e3e3"/>
          <stop offset="1" stop-color="#d8343a"/>
        </linearGradient>
        <linearGradient id="scriptTone" x1="0" y1="1" x2="1" y2="0">
          <stop offset="0" stop-color="var(--script-navy)"/>
          <stop offset="0.6" stop-color="var(--script-navy)"/>
          <stop offset="1" stop-color="var(--script-red)"/>
        </linearGradient>
        <linearGradient id="cityFill" x1="0" y1="0" x2="1" y2="1">
          <stop offset="0" stop-color="#5d8a4a"/>
          <stop offset="0.3" stop-color="#4f7fb8"/>
          <stop offset="0.55" stop-color="#b86a3c"/>
          <stop offset="0.8" stop-color="#6a9acb"/>
          <stop offset="1" stop-color="#7b8f45"/>
        </linearGradient>
      </defs>

      <rect class="front-photo" width="540" height="386" fill="url(#aerialTone)"
            role="img" aria-label="Soft aerial view of a green park and waterfront"/>

      <path class="top-band" d="M0 0 H540 V28 C420 34 300 60 0 110 Z" fill="url(#bandTone)"/>
      <path class="top-band-accent" d="M0 110 C300 60 420 34 540 28" fill="none" stroke="var(--accent-green)" stroke-width="4"/>

      <polygon class="badge-frame" points="440,22 486,22 510,66 486,110 440,110 416,66"
               fill="#ffffff" stroke="#c8c8c8" stroke-width="3"/>
      <polygon class="badge-art" points="443,30 483,30 503,66 483,102 443,102 423,66"
               fill="url(#badgeTone)" role="img" aria-label="Red cardinal with white dogwood blossoms"/>

      <g class="greeting" transform="rotate(-22 110 180)">
        <text class="greeting-script" x="30" y="170" font-size="50">Greetings</text>
        <text class="greeting-script" x="115" y="206" font-size="40">from</text>
      </g>

      <g class="state-name-group">
        <g transform="translate(34 338) rotate(-30)">
          <text class="state-name state-name--shadow" x="2" y="5">NORTH</text>
          <text class="state-name state-name--fill" x="0" y="0">NORTH</text>
        </g>
        <g transform="translate(146 364) rotate(-34)">
          <text class="state-name state-name--shadow" x="2" y="5">CAROLINA</text>
          <text class="state-name state-name--fill" x="0" y="0">CAROLINA</text>
        </g>
      </g>

      <line class="bottom-accent" x1="0" y1="378" x2="540" y2="378" stroke="var(--accent-green)" stroke-width="3"/>
      <rect class="bottom-band" x="0" y="380" width="540" height="6" fill="var(--band-blue)"/>
    </svg>
  </section>

</main>
</body>
</html>
```